Tidal Forge - Crypto Currency Miner Powered by Renewable Energy Website

We Need Web Pages Design for Website for Crypto Currency Miner

Serivices include:
Mining Rig Sales
Housing for Rigs turnkey on renewable energy grid
Cloud Mining term packages
Updates

http://www.vaultrigsurvey.example (Competitors sites)

Target Market(s)

Investers for Mining Rigs and terms for 1,2 or 3 years of Hash rate

Industry/Entity Type

Mining

Number of Pages Required

5+ page

Font styles to use
Sans Serif

Colors
add136
9bcb3c
606060
474747
ffc214
cadf82
fbee3e
876aae
6b449b

Requirements
Must have
• Pictures of Solar, Wind and power Factor Correction units
Nice to have
• e-commerce platform so contract terms can be purchased through website
Should not have
• Heavy construction equipment

```html
<!DOCTYPE html>
<html lang="en">
<head>
<meta charset="utf-8">
<title>Tidal Forge – Crypto Mining on Renewable Energy</title>
<link rel="stylesheet" href="https://fonts.googleapis.com/css2?family=Roboto:wght@400;500;700&family=Open+Sans:ital,wght@0,400;0,600;0,700;1,400&display=swap">
<style>
:root{
  --green-dark:#3f9a2a;
  --green:#add136;
  --green-mid:#9bcb3c;
  --green-pale:#f2f8e6;
  --lime:#cadf82;
  --grey:#606060;
  --grey-dark:#474747;
  --yellow:#ffc214;
  --purple:#6b449b;
  --purple-light:#876aae;
  --footer:#2b2a2a;
  --white:#fff;
}
*{box-sizing:border-box;margin:0;padding:0}
html,body{width:1200px;height:3191px;overflow:hidden}
body{font-family:"Open Sans",Arial,sans-serif;color:var(--grey);background:var(--white);font-size:12px}
h1,h2,h3,h4{font-family:"Roboto",Arial,sans-serif}
.wrap{width:716px;margin:0 auto;position:relative}
.btn{display:inline-block;font-family:"Roboto",sans-serif;font-weight:700;font-size:10px;text-transform:uppercase;padding:0 14px;line-height:30px;border-radius:3px;color:var(--grey-dark);background:var(--yellow)}
.btn.purple{background:var(--purple);color:var(--white)}

/* header */
.top{height:88px}
.top .wrap{display:flex;align-items:center;justify-content:space-between;height:88px}
.brand{display:flex;align-items:center;gap:8px;font-family:"Roboto",sans-serif;font-weight:700;font-size:20px;color:var(--green-dark)}
.brand i{width:26px;height:26px;border-radius:50%;background:var(--green-dark);display:block}
.contacts{display:flex;gap:26px}
.contact{display:flex;align-items:center;gap:7px;font-size:9px;line-height:1.3;color:var(--grey)}
.contact b{display:block;color:var(--grey-dark);font-weight:600;font-size:10px}
.contact .ico{width:26px;height:26px;border-radius:50%;background:var(--yellow);display:flex;align-items:center;justify-content:center}
.nav{height:30px;background:var(--green-mid)}
.nav .wrap{display:flex;align-items:center;height:30px}
.nav a{font-family:"Roboto",sans-serif;font-size:10px;font-weight:500;color:var(--white);text-transform:uppercase;padding:0 9px;line-height:30px;text-decoration:none}
.nav a.active{background:var(--yellow);color:var(--grey-dark)}
.search{margin-left:auto;width:128px;height:22px;border-radius:11px;background:var(--white);display:flex;align-items:center;gap:5px;padding:0 8px;font-size:9px;color:#999}

/* hero */
.hero{height:440px;position:relative;background:linear-gradient(180deg,#8fb3d6 0%,#dfe9ef 38%,#8aa4b8 55%,#4b6d84 70%,#5c9a36 86%,#3f7a22 100%);text-align:center;color:var(--white)}
.hero h1{padding-top:115px;font-size:37px;font-weight:700;color:#1f2a33}
.hero p{width:470px;margin:12px auto 0;font-size:10.5px;line-height:1.6;color:#33404a}
.hero .actions{margin-top:22px;display:flex;justify-content:center;gap:6px}
.dots{position:absolute;bottom:10px;left:50%;transform:translateX(-50%);display:flex;gap:4px}
.dots span{width:8px;height:8px;background:var(--white);transform:skewX(-20deg)}

/* services */
.services{height:456px;text-align:center}
.section-title{font-size:28px;font-weight:700;color:#222;padding-top:58px}
.svc-grid{display:flex;justify-content:space-between;margin-top:28px}
.svc{width:226px}
.ring{width:164px;height:164px;margin:0 auto;border-radius:50%;border:6px solid var(--green-dark);padding:7px}
.ring div{width:100%;height:100%;border-radius:50%;background:radial-gradient(circle at 50% 35%,#8fd14a,var(--green-dark));display:flex;align-items:center;justify-content:center}
.svc h3{font-size:13px;font-weight:700;color:#222;margin-top:20px;line-height:1.35}
.svc p{font-size:10.5px;line-height:1.6;margin-top:12px;padding:0 20px}

/* welcome */
.welcome{height:387px;position:relative;background:linear-gradient(100deg,#4f6f8c 0%,#7d97a8 35%,#e8c7a0 68%,#f2b46e 85%,#c9a07a 100%)}
.welcome-card{position:absolute;left:244px;top:51px;width:346px;height:285px;background:var(--purple);border-radius:12px;padding:26px 26px;color:var(--white)}
.welcome-card .kicker{display:flex;align-items:center;gap:8px}
.welcome-card .kicker i{width:36px;height:36px;border-radius:50%;border:2px solid var(--white);display:block}
.welcome-card small{display:block;font-size:14px;font-family:"Roboto",sans-serif}
.welcome-card h2{font-size:25px;font-weight:700;line-height:1}
.welcome-card p{font-size:10px;line-height:1.65;margin:10px 0 16px}

/* products */
.products{height:462px;text-align:center}
.products .section-title{padding-top:50px;font-size:28px}
.prod-grid{display:flex;justify-content:space-between;margin-top:24px}
.prod{width:226px;height:298px;background:var(--green-pale)}
.prod .photo{height:166px}
.prod h3{font-family:"Open Sans",sans-serif;font-size:11px;font-weight:600;color:var(--grey-dark);line-height:1.4;padding:16px 24px 0}
.prod .price{font-family:"Roboto",sans-serif;color:#e0201b;font-weight:700;font-size:17px;margin:6px 0 8px}
.prod .btn{font-size:9px;line-height:26px;padding:0 12px}

/* testimonials */
.voices-band{height:319px;background:linear-gradient(90deg,#2f8a2c 0%,#4aa53a 40%,#8cc63f 100%)}
.voices-band h2{padding-top:112px;color:var(--white);font-size:29px;line-height:1.05;font-weight:700}
.voices{height:202px;background:var(--green-pale);position:relative}
.quote-grid{display:flex;justify-content:space-between;position:relative;top:-38px}
.quote{width:226px;text-align:center}
.avatar{width:78px;height:78px;margin:0 auto;border-radius:50%;border:4px solid var(--white);box-shadow:0 0 0 3px var(--green-mid);background:linear-gradient(#d9cbbb,#a98e76)}
.quote p{font-style:italic;font-size:10px;line-height:1.6;margin-top:12px;padding:0 6px}
.quote b{display:block;margin-top:10px;color:#222;font-size:12px}
.arrow{position:absolute;top:80px;width:16px;height:16px;border-radius:50%;border:1px solid #999;display:flex;align-items:center;justify-content:center}

/* blog */
.lower{height:451px}
.lower .wrap{display:flex;justify-content:space-between;padding-top:53px}
.blog{width:410px}
.blog h2{font-size:21px;font-weight:500;color:#222;border-bottom:2px solid #ddd;padding-bottom:6px;position:relative}
.blog h2:after{content:"";position:absolute;left:0;bottom:-2px;width:150px;height:2px;background:var(--green-dark)}
.posts{display:flex;gap:14px;margin-top:18px}
.post{width:198px}
.post .photo{height:160px}
.post h3{font-family:"Open Sans",sans-serif;font-size:11px;font-weight:600;color:#222;line-height:1.4;margin-top:14px}
.post p{font-size:10px;line-height:1.55;margin-top:6px}
.post a{display:block;font-size:10px;color:var(--purple);margin-top:4px;text-decoration:none}
.why{width:288px;height:345px;margin-top:-15px;background:var(--purple);border-radius:12px;padding:22px 24px;color:var(--white)}
.why h2{font-size:21px;font-weight:500;margin-bottom:20px}
.reason{display:flex;gap:14px;margin-bottom:20px}
.reason svg{flex:none}
.reason h4{color:var(--yellow);font-size:13px;font-weight:700;margin-bottom:5px}
.reason p{font-size:10px;line-height:1.55;color:#e9e2f3}

/* footer */
.footer{height:357px;background:var(--footer);color:#bdbdbd}
.news{display:flex;align-items:center;padding-top:18px;gap:14px}
.news h3{color:var(--white);font-size:13px;line-height:1.1;font-weight:700;text-transform:uppercase}
.news .field{width:200px;height:26px;background:var(--white);font-size:9px;color:#999;padding:0 8px;line-height:26px;margin-left:10px}
.news .btn{line-height:26px;font-size:9px;margin-left:-10px;border-radius:0}
.social{margin-left:auto;display:flex;gap:6px}
.social i{width:22px;height:22px;border-radius:50%;border:1px solid #aaa;display:block}
.cols{display:flex;justify-content:space-between;margin-top:40px}
.col{width:170px}
.col h4{color:var(--white);font-size:12px;font-weight:700;margin-bottom:8px}
.col li{list-style:none;font-size:10px;line-height:1.65}
.pay{display:flex;justify-content:center;gap:6px;margin-top:50px}
.pay i{width:40px;height:22px;border-radius:2px;background:#8a8a8a;display:block}
.copy{text-align:center;font-size:10px;margin-top:16px}
</style>
</head>
<body>

<header class="top">
  <div class="wrap">
    <div class="brand"><i></i>Tidal Forge</div>
    <div class="contacts">
      <div class="contact"><span class="ico"><svg width="12" height="12" viewBox="0 0 24 24"><path fill="#474747" d="M6.6 10.8a15 15 0 0 0 6.6 6.6l2.2-2.2c.3-.3.7-.4 1-.2 1.1.4 2.3.6 3.6.6.6 0 1 .4 1 1V20c0 .6-.4 1-1 1A17 17 0 0 1 3 4c0-.6.4-1 1-1h3.5c.6 0 1 .4 1 1 0 1.3.2 2.5.6 3.6.1.3 0 .7-.2 1z"/></svg></span><div><b>555-014-2290</b>Toll Free Today!</div></div>
      <div class="contact"><span class="ico"><svg width="12" height="12" viewBox="0 0 24 24"><circle cx="12" cy="8" r="4" fill="#474747"/><path fill="#474747" d="M4 21c0-4.4 3.6-7 8-7s8 2.6 8 7z"/></svg></span><div><b>My Account</b>Create New Account</div></div>
      <div class="contact"><span class="ico"><svg width="12" height="12" viewBox="0 0 24 24"><path fill="#474747" d="M3 4h3l2.4 11h10l2-8H7.3"/><circle cx="9" cy="19" r="2" fill="#474747"/><circle cx="17" cy="19" r="2" fill="#474747"/></svg></span><div><b>Shopping Cart</b>0 Items – $0.00</div></div>
    </div>
  </div>
</header>

<nav class="nav">
  <div class="wrap">
    <a class="active">Home</a><a>About</a><a>Services</a><a>Products</a><a>Testimonials</a><a>Blog</a><a>Contact</a>
    <div class="search"><svg width="9" height="9" viewBox="0 0 24 24"><circle cx="10" cy="10" r="7" stroke="#888" stroke-width="3" fill="none"/><path d="M15 15l6 6" stroke="#888" stroke-width="3"/></svg>Enter keywords</div>
  </div>
</nav>

<section class="hero" role="img" aria-label="Rows of solar panels on green grass under a bright cloudy sky">
  <h1>Start The Tidal Forge Today!</h1>
  <p>Sed non mauris vitae erat consequat auctor eu in elit. Class aptent taciti sociosqu ad litora torquent per conubia nostra, per inceptos himenaeos. Mauris in erat justo. Nullam ac urna eu felis dapibus condimentum sit amet a augue.</p>
  <div class="actions"><span class="btn purple">Get Started Today!</span><span class="btn">Contact Now Today!</span></div>
  <div class="dots"><span></span><span></span><span></span><span></span><span></span></div>
</section>

<section class="services">
  <h2 class="section-title">Services We Provide</h2>
  <div class="wrap svc-grid">
    <div class="svc">
      <div class="ring"><div><svg width="70" height="70" viewBox="0 0 70 70" fill="none" stroke="#fff" stroke-width="3"><circle cx="35" cy="35" r="30"/><path d="M27 14v10M43 14v10M22 24h26v10a13 13 0 0 1-26 0zM35 47v10"/></svg></div></div>
      <h3>Mining Rig Sales</h3>
      <p>Class aptent taciti sociosqu ad litora torquent per conubia nostra, per inceptos himenaeos. Mauris in erat justo.</p>
    </div>
    <div class="svc">
      <div class="ring"><div><svg width="70" height="70" viewBox="0 0 70 70" fill="none" stroke="#fff" stroke-width="3"><path d="M16 30a20 20 0 0 1 36-8M54 40a20 20 0 0 1-36 8"/><path d="M52 12v10H42M18 58V48h10"/><path d="M37 24l-7 12h9l-6 11"/></svg></div></div>
      <h3>Housing for Rigs Turnkey<br>on Renewable Energy Grid</h3>
      <p>Class aptent taciti sociosqu ad litora torquent per conubia nostra, per inceptos himenaeos. Mauris in erat justo.</p>
    </div>
    <div class="svc">
      <div class="ring"><div><svg width="70" height="70" viewBox="0 0 70 70" fill="none" stroke="#fff" stroke-width="3"><path d="M20 50h30a10 10 0 0 0 0-20 14 14 0 0 0-27-3A11 11 0 0 0 20 50z"/><path d="M44 20l10-10M50 10h4v4"/></svg></div></div>
      <h3>Cloud Mining Term<br>Packages</h3>
      <p>Class aptent taciti sociosqu ad litora torquent per conubia nostra, per inceptos himenaeos. Mauris in erat justo.</p>
    </div>
  </div>
</section>

<section class="welcome" role="img" aria-label="Solar panel field with a wind turbine at sunset">
  <div class="welcome-card">
    <div class="kicker"><i></i><div><small>Welcome to</small><h2>The Tidal Forge</h2></div></div>
    <p>Nam nec tellus a odio tincidunt auctor a ornare odio. Sed non mauris vitae erat consequat auctor eu in elit. Class aptent taciti sociosqu ad litora torquent per conubia nostra, per inceptos himenaeos. Mauris in erat justo. Nullam ac urna eu felis dapibus condimentum sit amet a augue. Sed non fermentum nunc. Etiam pharetra, erat sed fermentum well feugiat, velit mauris egestas quam, ut aliquam massa nisl quis neque. Suspendisse in orci enim.</p>
    <span class="btn">Get Started Today!</span>
  </div>
</section>

<section class="products">
  <h2 class="section-title">Featured Products</h2>
  <div class="wrap prod-grid">
    <div class="prod"><div class="photo" role="img" aria-label="Wind turbines on a hillside under blue sky" style="background:linear-gradient(#2f6fc4,#8fb7e0 60%,#a08a5e)"></div><h3>Awesome Lorem ipsum dolor sit amet dosis lipsum it</h3><div class="price">$299.99</div><span class="btn">Add to Cart</span></div>
    <div class="prod"><div class="photo" role="img" aria-label="Solar panels in a field at sunrise" style="background:linear-gradient(160deg,#f8e27a,#5a8ec4 45%,#2f5d8a 70%,#4c8a2e)"></div><h3>Awesome Lorem ipsum dolor sit amet dosis lipsum it</h3><div class="price">$199.99</div><span class="btn">Add to Cart</span></div>
    <div class="prod"><div class="photo" role="img" aria-label="Close view of a wind turbine against the sky" style="background:linear-gradient(135deg,#3b7fb0,#a9cbe0 60%,#e8eef2)"></div><h3>Awesome Lorem ipsum dolor sit amet dosis lipsum it</h3><div class="price">$389.99</div><span class="btn">Add to Cart</span></div>
  </div>
</section>

<section class="voices-band" role="img" aria-label="Happy family standing in front of solar panels, tinted green">
  <div class="wrap"><h2>What About<br>Our Customer Say</h2></div>
</section>
<section class="voices">
  <span class="arrow" style="left:218px"><svg width="6" height="8" viewBox="0 0 6 8"><path d="M5 0L0 4l5 4z" fill="#888"/></svg></span>
  <span class="arrow" style="right:218px"><svg width="6" height="8" viewBox="0 0 6 8"><path d="M1 0l5 4-5 4z" fill="#888"/></svg></span>
  <div class="wrap quote-grid">
    <div class="quote"><div class="avatar" role="img" aria-label="Customer portrait"></div><p>"Duis sed odio sit amet nibh vulputate cursus a sit amet mauris. Morbi accumsan ipsum velit. Class aptent taciti sociosqu ad litora torquent per conubia nostra, per inceptos himenaeos."</p><b>- Owen Harlow</b></div>
    <div class="quote"><div class="avatar" role="img" aria-label="Customer portrait"></div><p>"Duis sed odio sit amet nibh vulputate cursus a sit amet mauris. Morbi accumsan ipsum velit. Class aptent taciti sociosqu ad litora torquent per conubia nostra, per inceptos himenaeos."</p><b>- Maren Vale</b></div>
    <div class="quote"><div class="avatar" role="img" aria-label="Customer portrait"></div><p>"Duis sed odio sit amet nibh vulputate cursus a sit amet mauris. Morbi accumsan ipsum velit. Class aptent taciti sociosqu ad litora torquent per conubia nostra, per inceptos himenaeos."</p><b>- Tomas Reyer</b></div>
  </div>
</section>

<section class="lower">
  <div class="wrap">
    <div class="blog">
      <h2>From The Blog</h2>
      <div class="posts">
        <div class="post"><div class="photo" role="img" aria-label="Solar panels and wind turbines under a blue sky" style="background:linear-gradient(#4f8fd0,#b9d5ec 55%,#3c6a94)"></div><h3>Awesome Lorem ipsum dolor sit amet dosis lipsum it</h3><p>Class aptent taciti sociosqu ad litora torquent per conubia nostra, per inceptos himenaeos. Mauris in erat justo.</p><a>Read More →</a></div>
        <div class="post"><div class="photo" role="img" aria-label="Wind turbines on green hills at dawn" style="background:linear-gradient(#8fb0d8,#f0dcc0 50%,#6f9a48)"></div><h3>Awesome Lorem ipsum dolor sit amet dosis lipsum it</h3><p>Class aptent taciti sociosqu ad litora torquent per conubia nostra, per inceptos himenaeos. Mauris in erat justo.</p><a>Read More →</a></div>
      </div>
    </div>
    <aside class="why">
      <h2>Why Choose Us</h2>
      <div class="reason"><svg width="32" height="32" viewBox="0 0 32 32" fill="none" stroke="#ffc214" stroke-width="2"><ellipse cx="12" cy="9" rx="8" ry="3"/><path d="M4 9v12c0 1.7 3.6 3 8 3s8-1.3 8-3V9"/><circle cx="23" cy="21" r="7"/></svg><div><h4>Best Price</h4><p>Proin condimentum fermentum nunc, etiam feugiat, velit mauris massa nisl quis neque.</p></div></div>
      <div class="reason"><svg width="32" height="32" viewBox="0 0 32 32" fill="none" stroke="#ffc214" stroke-width="2"><circle cx="16" cy="12" r="9"/><circle cx="16" cy="12" r="4"/><path d="M10 19l-3 10 5-2 3 4 1-9M22 19l3 10-5-2-3 4"/></svg><div><h4>Best Services</h4><p>Proin condimentum fermentum nunc, etiam feugiat, velit mauris massa nisl quis neque.</p></div></div>
      <div class="reason"><svg width="32" height="32" viewBox="0 0 32 32" fill="none" stroke="#ffc214" stroke-width="2"><path d="M16 3l11 4v8c0 7-5 12-11 14C10 27 5 22 5 15V7z"/><path d="M11 16l4 4 7-8"/></svg><div><h4>Guaranteed</h4><p>Proin condimentum fermentum nunc, etiam feugiat, velit mauris massa nisl quis neque.</p></div></div>
    </aside>
  </div>
</section>

<footer class="footer">
  <div class="wrap">
    <div class="news">
      <svg width="40" height="22" viewBox="0 0 40 22" fill="none" stroke="#ccc" stroke-width="1.5"><path d="M2 11L38 2 30 20 20 13z M20 13l-4 7"/></svg>
      <h3>Subscribe<br>Our Newsletter</h3>
      <div class="field">Enter Your Email</div>
      <span class="btn">Subscribe</span>
      <div class="social"><i></i><i></i><i></i><i></i><i></i></div>
    </div>
    <div class="cols">
      <div class="col"><h4>Navigation Links</h4><ul><li>Home</li><li>About</li><li>Services</li><li>Products</li><li>Testimonials</li><li>Blog</li><li>Contact</li></ul></div>
      <div class="col"><h4>Customer Service</h4><ul><li>About Us</li><li>Delivery Information</li><li>Privacy Policy</li><li>Terms &amp; Conditions</li><li>Contact Us</li><li>Returns</li><li>Site Map</li></ul></div>
      <div class="col"><h4>My Account</h4><ul><li>Order History</li><li>Wish List</li><li>Newsletter</li><li>Gift Vouchers</li><li>Affiliates</li><li>Specials</li></ul></div>
      <div class="col"><h4>Our Location</h4><ul><li>226, lorem ipsum dolor amet,</li><li>dosis sit sit - 44695</li><li>&nbsp;</li><li>T: 555 014 7780</li><li>F: 555 014 7781</li><li>E: info@tidalforge.example</li><li>www.tidalforge.example</li></ul></div>
    </div>
    <div class="pay"><i></i><i></i><i></i><i></i></div>
    <p class="copy">© 2018 The Tidal Forge. All Rights Reserved</p>
  </div>
</footer>

</body>
</html>
```